Website design for Puddle Jump Kidscare

I need a website designed for my daycare business, Puddle Jump Kidscare, now that I have a new logo. My former website was ok but simple and I did not have a logo yet. It also was created by me using a template and was entirely pink. I loved the bright, happy feel of it but worried it might not appeal as much to potential clients who have sons. Therefore, I need a site which will appeal to both genders while still keeping the cheerful color scheme of my new logo, which has pinks, blue, green and cream.
Updates

Reason: Hello! I am still trying to download my new logo and am sorry it is taking me so long. Hopefully I will it posted by the end of today (US Eastern Standard Time). Thank you all very much for your patience!

Hello! I have finally managed to upload my new logo for you to use in designing my website. I'm sorry it took so long and greatly appreciate your time and creative efforts! I look forward to seeing what is submitted based on my logo design and its style/colors.

Many thanks!

Reason: As I've been traveling and posted my logo file late, I am extending my deadline. I am now back and can focus on providing more and better feedback. I appreciate your patience and submissions very much!

Reason: I need more time to provide feedback and make decisions.

Industry/Entity Type

Daycare

Colors
0192cd
33a6d7
86cae7
cadf82
fbf289
add136
e34197

```html
<!DOCTYPE html>
<html lang="en">
<head>
<meta charset="utf-8">
<title>Puddle Jump Kidscare</title>
<link rel="stylesheet" href="https://fonts.googleapis.com/css2?family=Open+Sans:wght@400;600;700&display=swap">
<style>
:root{
  --pink-top:#fbb6d3;
  --pink-bottom:#fcc7de;
  --plum:#4a2f5c;
  --blue:#0d4fa8;
  --blue-dark:#0a3f8c;
  --nav-grey:#8a8a8a;
  --text:#555;
  --text-light:#888;
  --green:#1e8a3a;
  --green-bright:#3bb54a;
  --band:#f2f2f2;
  --line:#dcdcdc;
  --footer:#2b2b2b;
  --footer-text:#c8c8c8;
}
*{box-sizing:border-box;margin:0;padding:0}
html,body{width:991px;height:1200px;overflow:hidden;background:#fff}
body{font-family:"Open Sans",Arial,sans-serif;color:var(--text);position:relative}
.wrap{width:827px;margin:0 auto;position:relative}

.site-header{height:70px;background:linear-gradient(var(--pink-top),var(--pink-bottom))}
.site-header .wrap{height:70px;display:flex;align-items:center;justify-content:space-between}
.brand{font-size:29px;font-weight:600;color:var(--plum);letter-spacing:.2px}
.social{display:flex;gap:4px}
.social span{width:24px;height:24px;border-radius:50%;background:#3a3a3a;display:block}

.main-nav{height:51px;border-bottom:1px solid #eee}
.main-nav ul{list-style:none;display:flex;justify-content:space-between;width:802px;margin:0 0 0 103px;height:51px;align-items:center}
.main-nav a{font-size:12.3px;letter-spacing:.6px;color:var(--nav-grey);text-decoration:none;text-transform:uppercase}
.main-nav a.current{color:var(--blue)}

.hero{position:relative;height:388px;background:linear-gradient(180deg,#3f5a22 0%,#6f8f34 35%,#7fa83c 60%,#6b9a2e 100%)}
.hero .arrow{position:absolute;top:182px;width:20px;height:20px;border:1.5px solid #fff;border-radius:50%}
.hero .arrow svg{display:block}
.hero .prev{left:89px}.hero .next{right:99px}
.hero-caption{position:absolute;left:0;right:0;bottom:0;height:52px;background:rgba(40,40,30,.55);color:#fff;font-weight:700;font-size:20.5px;letter-spacing:.8px;text-align:center;line-height:52px}

.features{display:flex;justify-content:space-between;padding-top:32px;height:146px}
.feature{display:flex;width:265px}
.feature .icon{width:75px;height:75px;border-radius:50%;background:radial-gradient(circle at 40% 35%,#1f6fd0,var(--blue-dark));flex:none;display:flex;align-items:center;justify-content:center}
.feature h3{font-size:18.5px;font-weight:600;color:var(--blue);letter-spacing:.5px;margin:0 0 4px 5px;line-height:26px}
.feature p{font-size:11px;line-height:14px;color:var(--text-light);margin-left:6px}
.divider{border-top:1px solid var(--line)}

.welcome{text-align:center;padding:34px 40px 0;height:178px}
.welcome p{font-size:13.2px;line-height:19px}
.welcome .invite{font-size:16.5px;color:var(--green);margin-top:12px}

.news{height:137px;background:var(--band);border-top:1px solid #e2e2e2;border-bottom:1px solid #e2e2e2}
.news-head{display:flex;justify-content:space-between;align-items:center;height:48px;border-bottom:1px solid #d6d6d6;padding:0 10px 0 13px}
.news-head h2{font-size:16px;font-weight:600;color:var(--blue);letter-spacing:.3px}
.news-head .pager{display:flex;gap:4px}
.news-item{display:flex;padding:15px 0 0 15px}
.date{width:45px;height:50px;background:linear-gradient(#7a7a7a,#5a5a5a);color:#fff;text-align:center;flex:none}
.date b{display:block;font-weight:400;font-size:19px;line-height:26px;padding-top:3px}
.date small{font-size:11px}
.news-item p{font-size:11.8px;line-height:17px;color:#333;margin-left:10px;margin-top:-1px}

.hours{height:66px;text-align:center;font-size:26px;font-weight:600;letter-spacing:.8px;color:var(--green-bright);line-height:66px}

.contact{height:79px;background:var(--band)}
.contact .wrap{display:flex;height:79px;align-items:center;font-size:11.5px;color:#666}
.contact .item{display:flex;align-items:center;gap:10px}
.contact .item p{line-height:19px}

.site-footer{height:84px;background:var(--footer);color:var(--footer-text);text-align:center;font-size:11.3px}
.site-footer nav{padding-top:20px;letter-spacing:.3px}
.site-footer nav span{margin:0 9px}
.site-footer .copy{margin-top:14px;font-size:11px}
</style>
</head>
<body>
<header class="site-header">
  <div class="wrap">
    <div class="brand">Puddle Jump Kidscare</div>
    <div class="social" aria-label="Social links"><span></span><span></span><span></span><span></span></div>
  </div>
</header>

<nav class="main-nav">
  <ul>
    <li><a class="current" href="#">Home</a></li>
    <li><a href="#">About us</a></li>
    <li><a href="#">Services</a></li>
    <li><a href="#">Hours and Fees</a></li>
    <li><a href="#">Policies</a></li>
    <li><a href="#">Contact us</a></li>
    <li><a href="#">Gallery</a></li>
    <li><a href="#">Testimonials</a></li>
  </ul>
</nav>

<section class="hero" role="img" aria-label="Photo of children playing with a ball on a sunny lawn">
  <span class="arrow prev"><svg width="17" height="17" viewBox="0 0 17 17"><path d="M10 4.5 6 8.5l4 4" fill="none" stroke="#fff" stroke-width="1.6"/></svg></span>
  <span class="arrow next"><svg width="17" height="17" viewBox="0 0 17 17"><path d="M7 4.5l4 4-4 4" fill="none" stroke="#fff" stroke-width="1.6"/></svg></span>
  <div class="hero-caption">A PLAYSPACE WHERE CHILDREN CAN PLAY, CREATE, AND IMAGINE!</div>
</section>

<main class="wrap">
  <section class="features">
    <div class="feature">
      <div class="icon"><svg width="40" height="34" viewBox="0 0 40 34"><path d="M3 5h13c2 0 4 2 4 4v22c0-2-2-3-4-3H3zM37 5H24c-2 0-4 2-4 4v22c0-2 2-3 4-3h13z" fill="none" stroke="#fff" stroke-width="3"/></svg></div>
      <div><h3>LEARNING</h3><p>We develop age-appropriate activities that introduce and strengthen academic and social skills.</p></div>
    </div>
    <div class="feature">
      <div class="icon"><svg width="40" height="40" viewBox="0 0 40 40"><circle cx="20" cy="19" r="7" fill="none" stroke="#fff" stroke-width="2.5"/><path d="M17 27h6v5h-6z" fill="#fff"/><path d="M20 4v4M8 9l3 3M32 9l-3 3M5 19h4M31 19h4" stroke="#fff" stroke-width="2.5"/></svg></div>
      <div><h3>CREATIVITY</h3><p>We develop age-appropriate activities that introduce and strengthen academic and social skills.</p></div>
    </div>
    <div class="feature">
      <div class="icon"><svg width="40" height="36" viewBox="0 0 40 36"><path d="M8 4h20v16c0 3-2 5-5 5H13c-3 0-5-2-5-5z" fill="none" stroke="#fff" stroke-width="3"/><path d="M28 8h3c3 0 4 2 4 4s-1 4-4 4h-3" fill="none" stroke="#fff" stroke-width="3"/><rect x="4" y="29" width="30" height="3" rx="1.5" fill="#fff"/></svg></div>
      <div><h3>SHARING</h3><p>We develop age-appropriate activities that introduce and strengthen academic and social skills.</p></div>
    </div>
  </section>
  <div class="divider"></div>
  <section class="welcome">
    <p>Welcome to Puddle Jump Kidscare, a licensed Group Family Day Care, located in Brookfield's leafy Riverside district. We are located on a pretty, tree-lined block on Maple Row, between Elm and Oak Avenues. We are a few blocks from the Green Line tram and the Route 12 bus, and we offer flexible hourly childcare, making it as easy as possible for busy parents on the go to arrange their children's care.</p>
    <p class="invite">We invite you to learn more about us and hope you will visit us soon!</p>
  </section>
</main>

<section class="news">
  <div class="wrap">
    <div class="news-head">
      <h2>LATEST NEWS</h2>
      <div class="pager"><svg width="8" height="9"><path d="M7 0v9L0 4.5z" fill="#888"/></svg><svg width="8" height="9"><path d="M1 0v9l7-4.5z" fill="#888"/></svg></div>
    </div>
    <div class="news-item">
      <div class="date"><b>08</b><small>May</small></div>
      <p>Curabitur eget dapibus purus, in tempor mi. Donec tempor lorem ut aliquet scelerisque. Vivamus imperdiet lorem risus, sed feugiat augue luctus fermentum. Fusce feugiat ligula vitae pulvinar sollicitudin.</p>
    </div>
  </div>
</section>

<section class="hours">PLAYCARE HOURS ARE 8:00AM - 6:00PM</section>

<section class="contact">
  <div class="wrap">
    <div class="item" style="margin-left:10px;width:221px">
      <svg width="20" height="24" viewBox="0 0 20 24"><rect x="1" y="1" width="18" height="22" fill="none" stroke="#888" stroke-width="2"/><path d="M7 1v10l3-2 3 2V1" fill="#888"/></svg>
      <p>118 Maple Row<br>Brookfield, NY 10990</p>
    </div>
    <div class="item" style="width:210px">
      <svg width="24" height="24" viewBox="0 0 24 24"><path d="M4 3l5 0 2 5-3 2c1 3 3 5 6 6l2-3 5 2v5c-10 1-18-7-17-17z" fill="#888"/></svg>
      <p>Phone: (555) 014-2270</p>
    </div>
    <div class="item" style="width:206px">
      <svg width="24" height="24" viewBox="0 0 24 24"><rect x="1" y="8" width="4" height="15" fill="#888"/><rect x="6" y="10" width="17" height="13" fill="none" stroke="#888" stroke-width="2"/><rect x="9" y="2" width="11" height="8" fill="none" stroke="#888" stroke-width="2"/><path d="M10 14h2M14 14h2M18 14h2M10 18h2M14 18h2M18 18h2" stroke="#888" stroke-width="2"/></svg>
      <p>Fax : (555) 014-2271</p>
    </div>
    <div class="item">
      <svg width="24" height="16" viewBox="0 0 24 16"><rect width="24" height="16" fill="#999"/><path d="M0 0l12 9 12-9" fill="none" stroke="#eee" stroke-width="1.5"/></svg>
      <p>E-mail : hello@puddlejumpkids.com</p>
    </div>
  </div>
</section>

<footer class="site-footer">
  <nav>Home<span>|</span>About us<span>|</span>Services<span>|</span>Hours and Fees<span>|</span>Policies<span>|</span>Contact us<span>|</span>Gallery<span>|</span>Testimonials</nav>
  <p class="copy">Copyright © 2014 &nbsp; Puddle Jump Kidscare. &nbsp; All rights reserved.</p>
</footer>
</body>
</html>
```